Website for legal expungement services with button to qualify/disqualify potential clients

Brightpath Record Renewal, LLC is a law firm focusing in legal expungement servcies (allowing people to erase criminal court records, police records, proseution files, etc). I want a more modern look which exudes confidence in the services. I am looking for a clean website that looks very polished. I want to keep the pages to a minimum, as I want the page not so much to answer questions, but to direct traffic to contact the law office. I would like the main focus point to be an button which would take a client through a series of questions to see if they would qualify for the services; this serves two purposes 1) to collect contact info for future marketing via email and 2) eliminate individuals who we are currently unable to help. A current theme that I have played around with are "Change so much, you'll need to reintroduce yourself" alongside a picture of a guys hand outstretched.
On the landing page, I would like a very brief and to the point explanation of what the service would be (i.e. "Leave your past in the past; expunge all your criminal records" ), followed by a list of benefits that it provides. (NB: included is a file "law post card-02" that includes the main benefits to expungement). Also included are two logo files for a more updated logo I currently use ("BRR Logo" and BRR Logo2") (NB: I'm open to revisions on this as well). Lastly, I've had two very minor 'ads' that I did ("postcard back" and "KVT Ad") that I like the idea of.

Target Market(s)

Middle/upper-middle class, mostly male, people with a criminal record or criminal accusation

Industry/Entity Type

Legal Services

Coding

Coded - Design and coding required

Requirements
Must have
• Button that attracts attention up front (possibly stand out coloring) to click to open up a series of questions to qualify/eliminate prospects, and simultaneously gather their info. Also, must be mobile friendly.

```html
<!DOCTYPE html>
<html lang="en">
<head>
<meta charset="utf-8">
<title>Brightpath Record Renewal, LLC</title>
<link href="https://fonts.googleapis.com/css2?family=Poppins:wght@400;500;600;700&family=Lora:wght@400;500;600;700&display=swap" rel="stylesheet">
<style>
:root{
  --navy:#0b3370;
  --navy-deep:#082a5e;
  --blue:#0a66d6;
  --sky:#8ec3ff;
  --pale:#eef5fd;
  --gold:#f5a623;
  --ink:#1b1b1b;
  --text:#4b4f58;
  --line:#cfd9e8;
  --white:#ffffff;
}
*{box-sizing:border-box;margin:0;padding:0}
html,body{width:1200px;height:4107px;overflow:hidden;background:var(--white)}
body{position:relative;font-family:'Lora',serif;color:var(--ink)}
.abs{position:absolute}
.sans{font-family:'Poppins',sans-serif}

/* header */
.site-header{left:0;top:0;width:1200px;height:70px}
.header-light{left:0;top:0;width:464px;height:70px;background:var(--white)}
.header-dark{left:464px;top:0;width:736px;height:70px;background:var(--navy)}
.brand{display:flex;align-items:center}
.brand-mark{font-family:'Poppins',sans-serif;font-weight:500;color:var(--navy);letter-spacing:6px;display:flex;align-items:center;gap:8px}
.brand-mark i{display:block;background:var(--blue)}
.brand-rule{width:1px;background:var(--navy);margin:0 22px}
.brand-name{font-family:'Lora',serif;color:var(--navy);text-transform:uppercase;line-height:1.05;letter-spacing:.6px}
.call-label{left:500px;top:26px;font-family:'Poppins',sans-serif;font-size:13px;color:#dfe7f4}
.call-rule{left:617px;top:34px;width:50px;height:1px;background:#8ea3c6}
.call-phone{left:686px;top:25px;font-family:'Poppins',sans-serif;font-size:13.5px;font-weight:600;color:var(--white);display:flex;align-items:center;gap:10px}
.btn{font-family:'Poppins',sans-serif;font-weight:500;color:var(--white);display:flex;align-items:center;justify-content:center;white-space:nowrap}
.btn-blue{background:var(--blue)}
.btn-navy{background:var(--navy);clip-path:polygon(0 0,100% 0,100% 70%,92% 100%,0 100%)}
.btn-qualify{background:var(--gold);color:var(--navy-deep);font-weight:600;gap:10px;box-shadow:0 6px 18px rgba(245,166,35,.45)}

/* hero */
.hero-photo{left:0;top:70px;width:1200px;height:568px;background:linear-gradient(180deg,#4f86c5 0%,#7fb0dd 35%,#6f93a8 62%,#46603f 82%,#37442f 100%)}
.hero-panel{left:160px;top:231px;width:549px;height:191px;background:rgba(214,232,250,.72)}
.hero-title{left:200px;top:262px;font-family:'Lora',serif;font-size:30px;line-height:48px;color:var(--navy);text-transform:uppercase;letter-spacing:.5px;font-weight:400}
.hero-accent{left:158px;top:296px;width:4px;height:64px;background:var(--navy)}

.sq{position:absolute;z-index:2}

/* about */
.section-title{font-family:'Poppins',sans-serif;font-weight:600;color:var(--ink);text-align:center}
.about-lead{left:200px;top:818px;width:360px;font-size:13.5px;line-height:23.2px;font-weight:600;text-transform:uppercase;text-align:center;color:#222}
.photo{display:block}
.cut-br{clip-path:polygon(0 0,100% 0,100% 88%,94% 100%,0 100%)}
.shadow-frame{background:#cfe0f6}
.about-copy{left:631px;top:1098px;width:385px;font-size:13.4px;line-height:24px;color:var(--text)}
.divider-v{left:599px;top:1080px;width:1px;height:260px;background:var(--line)}
.rating-badge{left:483px;top:1049px;width:107px;height:90px;background:var(--white);display:flex;flex-direction:column;align-items:center;padding-top:6px}
.rating-badge b{font-family:'Poppins',sans-serif;font-size:21px;font-weight:600;color:var(--navy)}
.rating-badge b span{color:var(--gold);font-size:17px}
.rating-badge .badge-shape{width:80px;height:22px;border-radius:11px;background:#d9e3f1;margin-top:4px}
.rating-badge small{font-family:'Poppins',sans-serif;font-size:10px;color:#666;margin-top:3px}

/* services */
.services-band{left:0;top:1415px;width:1200px;height:378px;background:var(--pale)}
.service-card{top:1487px;width:200px;height:232px;border:1px solid #d9e4f2;padding:9px}
.service-inner{width:100%;height:100%;background:var(--white);clip-path:polygon(0 0,90% 0,100% 7%,100% 100%,12% 100%,0 93%);display:flex;flex-direction:column;align-items:center;padding-top:30px;text-align:center}
.service-inner svg{width:56px;height:56px}
.service-inner h3{font-family:'Poppins',sans-serif;font-weight:400;font-size:14px;color:#222;margin-top:14px}
.service-inner p{font-size:12px;line-height:19px;color:var(--text);margin-top:6px;width:140px}

/* benefits */
.block-title{font-family:'Poppins',sans-serif;font-weight:600;color:var(--ink)}
.title-rule{height:2px;width:50px;background:var(--navy)}
.benefit-photo{top:1859px;width:194px;height:208px}
.benefit-caption{top:2078px;width:176px;font-size:13.5px;line-height:21px;color:#333}
.read-more{font-family:'Poppins',sans-serif;font-size:11.5px;font-weight:600;color:var(--navy);text-decoration:underline;text-underline-offset:3px}
.arrow-btn{width:37px;height:37px;display:flex;align-items:center;justify-content:center}
.arrow-outline{border:1px solid #b8c6da;background:var(--white)}
.arrow-solid{background:var(--navy)}

/* lists */
.check-list{list-style:none}
.check-list li{position:relative;padding-left:34px;font-size:13.5px;color:#222;line-height:19px}
.check-list li svg{position:absolute;left:0;top:2px}
.check-list a{color:var(--navy);text-decoration:none}

/* testimonials */
.testimonial-band{left:0;top:2949px;width:1200px;height:494px;background:var(--pale)}
.quote-card{top:3073px;width:410px;height:208px;background:var(--white);box-shadow:0 3px 14px rgba(20,50,110,.06);text-align:center;padding-top:34px}
.quote-card p{font-size:13.6px;line-height:24px;color:var(--text);width:355px;margin:14px auto 0}
.quote-tail{width:16px;height:16px;background:var(--white);transform:rotate(45deg)}
.avatar{width:54px;height:54px;border-radius:50%;border:2px solid var(--white)}
.client-name{font-size:13.5px;color:#222;width:160px;text-align:center}

/* contact */
.contact-band{left:0;top:3443px;width:1200px;height:330px;background:linear-gradient(90deg,#1c3f8d 0%,#2f4ea0 55%,#4a63b6 100%)}
.contact-box{left:161px;top:3531px;width:875px;height:369px;background:var(--white);box-shadow:0 10px 30px rgba(10,30,70,.14)}
.contact-panel{left:684px;top:3531px;width:352px;height:369px;background:var(--navy-deep);border:3px solid var(--white);outline:1px solid #d5deeb}
.field{border:1px solid #d8dde5;background:var(--white);font-size:11px;color:#777;padding:10px 11px}
.detail-row{display:flex;align-items:center;gap:14px;color:var(--white)}
.detail-icon{width:30px;height:30px;border:1px solid #8aa0c6;display:flex;align-items:center;justify-content:center;flex:none}
.detail-rule{height:1px;background:#3b5a91}
.social{display:flex;align-items:center;gap:10px;font-size:12px;color:var(--white)}

/* footer */
.footer-nav{left:585px;top:3956px;font-size:12.5px;color:#333}
.footer-nav span{position:absolute;white-space:nowrap}
.copyright-band{left:0;top:4036px;width:1200px;height:71px;background:#f1f3f7}
.copyright{left:0;width:1200px;text-align:center;top:4062px;font-family:'Poppins',sans-serif;font-size:13px;color:var(--navy)}
</style>
</head>
<body>

<header class="abs site-header">
  <div class="abs header-light"></div>
  <div class="abs header-dark"></div>
  <div class="abs brand" style="left:163px;top:18px;height:36px">
    <div class="brand-mark" style="font-size:19px"><i style="width:10px;height:10px"></i>BRR</div>
    <div class="brand-rule" style="height:36px"></div>
    <div class="brand-name" style="font-size:11.5px">Brightpath<br>Record Renewal</div>
  </div>
  <div class="abs call-label">Call Us Today</div>
  <div class="abs call-rule"></div>
  <div class="abs call-phone">
    <svg width="18" height="18" viewBox="0 0 24 24" fill="none" stroke="#fff" stroke-width="1.6"><path d="M5 3h4l2 5-2.5 1.5a11 11 0 0 0 6 6L16 13l5 2v4a2 2 0 0 1-2 2A16 16 0 0 1 3 5a2 2 0 0 1 2-2z"/></svg>
    555-014-2286
  </div>
  <a class="abs btn btn-blue" style="left:910px;top:14px;width:129px;height:42px;font-size:13px">Contact Us</a>
</header>

<section class="hero">
  <div class="abs hero-photo" role="img" aria-label="City skyline with a golden winged monument under a blue sky"></div>
  <div class="abs hero-panel"></div>
  <div class="abs hero-accent"></div>
  <h1 class="abs hero-title">Change so much...<br>You'll need&nbsp; to reintroduce<br>yourself</h1>
  <a class="abs btn btn-qualify" style="left:161px;top:438px;width:232px;height:44px;font-size:14px">
    See If You Qualify
    <svg width="18" height="12" viewBox="0 0 18 12" fill="none" stroke="#082a5e" stroke-width="1.8"><path d="M1 6h16M12 1l5 5-5 5"/></svg>
  </a>
</section>

<div class="sq" style="left:1033px;top:650px;width:67px;height:26px;background:var(--navy);outline:6px solid #fff;box-shadow:0 0 0 7px #dfe5ee"></div>
<div class="sq" style="left:1132px;top:658px;width:43px;height:43px;background:var(--blue);border:6px solid #fff;box-shadow:0 0 0 1px #cfd7e4"></div>

<section class="about">
  <h2 class="abs section-title" style="left:0;top:700px;width:1200px;font-size:28px">ABOUT US</h2>
  <p class="abs about-lead">Brightpath Record Renewal is 5-star rated firm, which has been formed with the passing of the State Expungement Law of 2020. It is a subdivision of the Harlow Law Firm, and since its creation has helped over 100 local citizens successfully expunge their criminal records.</p>

  <div class="abs shadow-frame cut-br" style="left:606px;top:783px;width:441px;height:290px"></div>
  <div class="abs photo cut-br" style="left:599px;top:776px;width:440px;height:288px;background:linear-gradient(135deg,#dfe4ea 0%,#b7c0ca 45%,#6f6a62 75%,#3c332c 100%)" role="img" aria-label="Lawyer and client at a desk with a wooden gavel"></div>

  <div class="abs shadow-frame" style="left:202px;top:1053px;width:357px;height:222px;clip-path:polygon(0 0,100% 0,100% 100%,8% 100%,0 88%)"></div>
  <div class="abs photo" style="left:209px;top:1046px;width:343px;height:220px;background:linear-gradient(160deg,#2e3a48 0%,#8b93a0 40%,#c7ccd3 55%,#9a4a4f 75%,#4d5566 100%);clip-path:polygon(0 0,100% 0,100% 100%,8% 100%,0 88%)" role="img" aria-label="American flags hanging from a tall office building"></div>
  <div class="abs rating-badge">
    <b>5.0 <span>★</span></b>
    <div class="badge-shape"></div>
    <small>Reviews</small>
  </div>
  <a class="abs btn btn-navy" style="left:276px;top:1294px;width:209px;height:47px;font-size:12.5px;letter-spacing:1.2px">READ MORE ALL ABOUT</a>

  <div class="abs divider-v"></div>
  <p class="abs about-copy">Lorem ipsum dolor sit amet, consectetuer adipiscing elit, sed diam nonummy nibh euismod tincidunt ut laoreet dolore magna aliquam erat volutpat. Ut wisi enim ad minim veniam, quis nostrud exerci tation ullamcorper suscipit lobortis nisl ut aliquip ex ea commodo consequat. Duis autem vel eum iriure dolor in hendrerit in vulputate velit esse molestie consequat, vel illum dolore eu feugiat nulla facilisis at vero eros et accumsan et iusto ..</p>
</section>

<section class="services">
  <div class="abs services-band"></div>

  <div class="abs service-card" style="left:161px">
    <div class="service-inner">
      <svg viewBox="0 0 56 56" fill="none" stroke="#1f4a8e" stroke-width="1.8" stroke-linejoin="round" stroke-linecap="round"><path d="M4 22l8-6 10 4 8-4 8 2 14 4"/><path d="M4 22l4 12 6 2 8 8 4-1 4 4 4-2 4 2 4-4 8-8 2-11"/><path d="M22 20l-6 8 4 3 8-6"/><path d="M14 36l4 4M20 38l4 4M26 41l3 3"/></svg>
      <h3>Get Legal Advice</h3>
      <p>Lorem ipsum dolor sit amet, consectetuer adipiscing elit, sed</p>
    </div>
  </div>
  <div class="abs service-card" style="left:386px">
    <div class="service-inner">
      <svg viewBox="0 0 56 56" fill="none" stroke="#1f4a8e" stroke-width="1.8" stroke-linejoin="round"><path d="M12 4h22l10 10v38H12z"/><path d="M34 4v10h10"/><path d="M19 22h18M19 29h18M19 36h18M19 43h10"/></svg>
      <h3>Document Reviewing</h3>
      <p>Lorem ipsum dolor sit amet, consectetuer adipiscing elit, sed</p>
    </div>
  </div>
  <div class="abs service-card" style="left:611px">
    <div class="service-inner">
      <svg viewBox="0 0 56 56" fill="none" stroke="#1f4a8e" stroke-width="1.8" stroke-linejoin="round"><rect x="8" y="14" width="40" height="26" rx="2" transform="rotate(-30 28 27)"/><circle cx="28" cy="27" r="7"/><path d="M28 23v8M26 25h3a1.5 1.5 0 0 1 0 3h-2a1.5 1.5 0 0 0 0 3h3"/><path d="M10 44l6 6M40 6l6 6"/></svg>
      <h3>Discounted Rates</h3>
      <p>Lorem ipsum dolor sit amet, consectetuer adipiscing elit, sed</p>
    </div>
  </div>
  <div class="abs service-card" style="left:836px">
    <div class="service-inner">
      <svg viewBox="0 0 56 56" fill="none" stroke="#1f4a8e" stroke-width="1.8" stroke-linejoin="round"><rect x="16" y="6" width="12" height="22" rx="2" transform="rotate(-45 22 17)"/><path d="M26 24l18 18-4 4-18-18"/><path d="M6 46h24v6H6z"/><path d="M10 46v-4h16v4"/></svg>
      <h3>Always My Best</h3>
      <p>Lorem ipsum dolor sit amet, consectetuer adipiscing elit, sed</p>
    </div>
  </div>
</section>

<div class="sq" style="left:30px;top:1344px;width:42px;height:42px;background:var(--blue);border:6px solid #fff;box-shadow:0 0 0 1px #cfd7e4"></div>
<div class="sq" style="left:99px;top:1363px;width:78px;height:78px;background:var(--navy);border:8px solid #fff;box-shadow:0 0 0 1px #cfd7e4"></div>
<div class="sq" style="left:5px;top:1403px;width:64px;height:64px;background:var(--sky);border:7px solid #fff;box-shadow:0 0 0 1px #cfd7e4"></div>

<section class="benefits">
  <h2 class="abs block-title" style="left:175px;top:1924px;font-size:29px;line-height:37px;letter-spacing:.5px">BENEFITS TO<br>EXPUNGING</h2>
  <div class="abs title-rule" style="left:175px;top:2005px"></div>
  <a class="abs btn btn-navy" style="left:175px;top:2034px;width:114px;height:45px;font-size:12.5px;letter-spacing:1px">VIEW ALL</a>

  <div class="abs benefit-photo" style="left:413px;background:linear-gradient(160deg,#eef0f2 0%,#c9c4bf 45%,#6b5446 70%,#f3f3f3 100%)" role="img" aria-label="Smiling woman reaching out to shake hands"></div>
  <div class="abs benefit-photo" style="left:628px;background:linear-gradient(160deg,#dfe3e7 0%,#9aa3ad 45%,#4d5560 75%,#e9ecef 100%)" role="img" aria-label="Professionals meeting around a table in an office"></div>
  <div class="abs benefit-photo" style="left:845px;background:linear-gradient(160deg,#e4e7ea 0%,#aab1ba 40%,#3f4a5c 70%,#cfd4da 100%)" role="img" aria-label="Colleagues reviewing work at a laptop"></div>

  <p class="abs benefit-caption" style="left:420px">More and better job opportunities leading to higher income</p>
  <a class="abs read-more" style="left:425px;top:2149px">READ MORE</a>
  <p class="abs benefit-caption" style="left:636px">Loan qualification and better loan rates</p>
  <a class="abs read-more" style="left:636px;top:2127px">READ MORE</a>
  <p class="abs benefit-caption" style="left:852px;width:160px">Removing the stigma of having a criminal record</p>
  <a class="abs read-more" style="left:852px;top:2149px">READ MORE</a>

  <div class="abs arrow-btn arrow-outline" style="left:1068px;top:1928px"><svg width="18" height="12" viewBox="0 0 18 12" fill="none" stroke="#6a7a93" stroke-width="1.4"><path d="M17 6H1M6 1L1 6l5 5"/></svg></div>
  <div class="abs arrow-btn arrow-solid" style="left:1068px;top:1981px"><svg width="18" height="12" viewBox="0 0 18 12" fill="none" stroke="#fff" stroke-width="1.6"><path d="M1 6h16M12 1l5 5-5 5"/></svg></div>
</section>

<section class="records">
  <div class="abs shadow-frame" style="left:168px;top:2242px;width:410px;height:288px;clip-path:polygon(0 0,100% 0,100% 88%,91% 100%,0 100%)"></div>
  <div class="abs photo" style="left:161px;top:2235px;width:410px;height:288px;background:linear-gradient(150deg,#d7dbe0 0%,#eef0f2 35%,#5d6470 60%,#2c313a 85%,#bfc5cc 100%);clip-path:polygon(0 0,100% 0,100% 88%,91% 100%,0 100%)" role="img" aria-label="Woman holding a certificate while colleagues applaud"></div>

  <h2 class="abs block-title" style="left:626px;top:2246px;font-size:23px;line-height:32px">How Your Records Are<br>Seen By The Public:</h2>
  <div class="abs title-rule" style="left:626px;top:2322px;width:48px"></div>
  <ul class="abs check-list" style="left:636px;top:2346px;width:400px">
    <li style="margin-bottom:11px"><svg width="16" height="16" viewBox="0 0 16 16" fill="none" stroke="#9bb4d6" stroke-width="1.6"><path d="M3 13L13 3M6 3h7v7"/></svg>Public reporting <a>(www.statecourts.example)</a></li>
    <li style="margin-bottom:11px"><svg width="16" height="16" viewBox="0 0 16 16" fill="none" stroke="#9bb4d6" stroke-width="1.6"><path d="M3 13L13 3M6 3h7v7"/></svg>Police reports</li>
    <li style="margin-bottom:11px"><svg width="16" height="16" viewBox="0 0 16 16" fill="none" stroke="#9bb4d6" stroke-width="1.6"><path d="M3 13L13 3M6 3h7v7"/></svg>State Department of Public Safety</li>
    <li style="margin-bottom:11px"><svg width="16" height="16" viewBox="0 0 16 16" fill="none" stroke="#9bb4d6" stroke-width="1.6"><path d="M3 13L13 3M6 3h7v7"/></svg>District attorney prosecution files</li>
    <li><svg width="16" height="16" viewBox="0 0 16 16" fill="none" stroke="#9bb4d6" stroke-width="1.6"><path d="M3 13L13 3M6 3h7v7"/></svg>Court records</li>
  </ul>

  <div class="sq" style="left:1076px;top:2482px;width:49px;height:49px;background:var(--sky);border:6px solid #fff;box-shadow:0 0 0 1px #cfd7e4"></div>
  <div class="sq" style="left:962px;top:2502px;width:73px;height:73px;background:var(--navy);border:8px solid #fff;box-shadow:0 0 0 1px #cfd7e4"></div>
  <div class="sq" style="left:1066px;top:2556px;width:39px;height:39px;background:var(--blue);border:5px solid #fff;box-shadow:0 0 0 1px #cfd7e4"></div>
</section>

<section class="cases">
  <h2 class="abs block-title" style="left:204px;top:2626px;font-size:23px;line-height:32px">What Types Of Cases<br>Qualify:</h2>
  <div class="abs title-rule" style="left:204px;top:2701px;width:48px"></div>
  <ul class="abs check-list" style="left:214px;top:2724px;width:360px">
    <li style="margin-bottom:11px"><svg width="16" height="16" viewBox="0 0 16 16" fill="none" stroke="#9bb4d6" stroke-width="1.6"><path d="M3 13L13 3M6 3h7v7"/></svg>Criminal accusations that were dismissed</li>
    <li style="margin-bottom:11px"><svg width="16" height="16" viewBox="0 0 16 16" fill="none" stroke="#9bb4d6" stroke-width="1.6"><path d="M3 13L13 3M6 3h7v7"/></svg>Criminal cases that went into a diversionary program</li>
    <li><svg width="16" height="16" viewBox="0 0 16 16" fill="none" stroke="#9bb4d6" stroke-width="1.6"><path d="M3 13L13 3M6 3h7v7"/></svg>Convictions</li>
  </ul>

  <div class="abs shadow-frame" style="left:623px;top:2599px;width:416px;height:290px;clip-path:polygon(0 0,100% 0,100% 100%,11% 100%,0 86%)"></div>
  <div class="abs photo" style="left:630px;top:2592px;width:409px;height:290px;background:linear-gradient(170deg,#2a4472 0%,#5873a0 40%,#34507f 70%,#1f3660 100%);clip-path:polygon(0 0,100% 0,100% 100%,11% 100%,0 86%)" role="img" aria-label="Blue-toned office crowd beneath a city skyline with a large question mark"></div>
</section>

<section class="testimonials">
  <div class="abs testimonial-band"></div>
  <h2 class="abs section-title" style="left:0;top:3000px;width:1200px;font-size:21px">WHAT OUR CLIENT SAY</h2>
  <div class="abs title-rule" style="left:577px;top:3036px;width:48px"></div>

  <div class="abs quote-card" style="left:175px">
    <svg width="34" height="26" viewBox="0 0 34 26" fill="#0b3370"><path d="M0 0h14v13c0 7-4 12-11 13l-1-4c4-1 6-4 6-9H0zM19 0h14v13c0 7-4 12-11 13l-1-4c4-1 6-4 6-9h-8z"/></svg>
    <p>Lorem ipsum dolor sit amet, consectetuer adipiscing elit, sed diam nonummy nibh euismod tincidunt ut laoreet dolore magna aliquam erat volutpat. Ut wisi enim ad minim veniam, quis nostrud exerci tation ullamcorper suscipit lobo..</p>
  </div>
  <div class="abs quote-tail" style="left:372px;top:3273px"></div>
  <div class="abs quote-card" style="left:615px">
    <svg width="34" height="26" viewBox="0 0 34 26" fill="#0b3370"><path d="M0 0h14v13c0 7-4 12-11 13l-1-4c4-1 6-4 6-9H0zM19 0h14v13c0 7-4 12-11 13l-1-4c4-1 6-4 6-9h-8z"/></svg>
    <p>Lorem ipsum dolor sit amet, consectetuer adipiscing elit, sed diam nonummy nibh euismod tincidunt ut laoreet dolore magna aliquam erat volutpat. Ut wisi enim ad minim veniam, quis nostrud exerci tation ullamcorper suscipit lobo..</p>
  </div>
  <div class="abs quote-tail" style="left:812px;top:3273px"></div>

  <div class="abs avatar" style="left:352px;top:3300px;background:linear-gradient(160deg,#6a4a3a,#2e2a2c)" role="img" aria-label="Client portrait"></div>
  <div class="abs client-name" style="left:299px;top:3359px">Dev Ramanathan</div>
  <div class="abs avatar" style="left:794px;top:3298px;background:linear-gradient(160deg,#c9a99a,#7a4c44)" role="img" aria-label="Client portrait"></div>
  <div class="abs client-name" style="left:741px;top:3356px">Lena Ortiz</div>

  <div class="abs arrow-btn arrow-outline" style="left:121px;top:3163px;width:40px;height:40px"><svg width="18" height="12" viewBox="0 0 18 12" fill="none" stroke="#6a7a93" stroke-width="1.4"><path d="M17 6H1M6 1L1 6l5 5"/></svg></div>
  <div class="abs arrow-btn arrow-solid" style="left:1039px;top:3163px;width:40px;height:40px"><svg width="18" height="12" viewBox="0 0 18 12" fill="none" stroke="#fff" stroke-width="1.6"><path d="M1 6h16M12 1l5 5-5 5"/></svg></div>
</section>

<section class="contact">
  <div class="abs contact-band"></div>
  <div class="abs contact-box"></div>
  <h2 class="abs section-title" style="left:161px;top:3564px;width:523px;font-size:23px">CONTACT US</h2>
  <div class="abs title-rule" style="left:399px;top:3603px;width:48px"></div>
  <div class="abs field" style="left:196px;top:3625px;width:217px;height:36px">Name*</div>
  <div class="abs field" style="left:429px;top:3625px;width:217px;height:36px">Email</div>
  <div class="abs field" style="left:196px;top:3678px;width:217px;height:36px">Phone No</div>
  <div class="abs field" style="left:429px;top:3678px;width:217px;height:36px">Subject</div>
  <div class="abs field" style="left:196px;top:3730px;width:450px;height:76px">Message</div>
  <a class="abs btn" style="left:375px;top:3826px;width:95px;height:41px;background:#151515;font-size:12.5px;letter-spacing:1.4px;font-weight:600">SUBMIT</a>

  <div class="abs contact-panel"></div>
  <h2 class="abs sans" style="left:711px;top:3570px;font-size:23px;font-weight:500;color:#fff;letter-spacing:.5px">CONTACT DETAILS</h2>
  <div class="abs" style="left:711px;top:3608px;width:46px;height:2px;background:#fff"></div>

  <div class="abs detail-row" style="left:711px;top:3628px;width:300px;font-size:12px;line-height:18px">
    <div class="detail-icon"><svg width="12" height="16" viewBox="0 0 12 16" fill="none" stroke="#fff" stroke-width="1.4"><path d="M6 15s5-5.5 5-9A5 5 0 0 0 1 6c0 3.5 5 9 5 9z"/><circle cx="6" cy="6" r="1.8"/></svg></div>
    <span>123, Lorem Ipsum dolor Lorem Ipsum is dummy text.</span>
  </div>
  <div class="abs detail-rule" style="left:711px;top:3683px;width:300px"></div>
  <div class="abs detail-row" style="left:711px;top:3700px;font-size:22px">
    <div class="detail-icon"><svg width="14" height="14" viewBox="0 0 24 24" fill="#fff"><path d="M5 3h4l2 5-2.5 1.5a11 11 0 0 0 6 6L16 13l5 2v4a2 2 0 0 1-2 2A16 16 0 0 1 3 5a2 2 0 0 1 2-2z"/></svg></div>
    <span>555-014-2286</span>
  </div>
  <div class="abs detail-rule" style="left:711px;top:3746px;width:300px"></div>
  <div class="abs detail-row" style="left:711px;top:3763px;font-size:12.5px">
    <div class="detail-icon"><svg width="14" height="11" viewBox="0 0 14 11" fill="#fff"><path d="M0 0h14v11H0z"/><path d="M0 0l7 6 7-6" stroke="#082a5e" stroke-width="1.3" fill="none"/></svg></div>
    <span>info@brightpathrenewal.com</span>
  </div>
  <div class="abs detail-rule" style="left:711px;top:3808px;width:300px"></div>
  <div class="abs" style="left:711px;top:3825px;display:flex;gap:18px">
    <div class="social"><div class="detail-icon"><svg width="10" height="10"><rect width="10" height="10" fill="#fff"/></svg></div>Friendly</div>
    <div class="social"><div class="detail-icon"><svg width="10" height="10"><circle cx="5" cy="5" r="5" fill="#fff"/></svg></div>Updates</div>
    <div class="social"><div class="detail-icon"><svg width="10" height="10"><rect width="10" height="10" fill="#fff"/></svg></div>Network</div>
  </div>
</section>

<footer>
  <div class="abs brand" style="left:161px;top:3935px;height:70px">
    <div class="brand-mark" style="font-size:26px;letter-spacing:8px"><i style="width:12px;height:12px"></i>BRR</div>
    <div class="brand-rule" style="height:80px;margin:0 26px 0 20px"></div>
    <div class="brand-name" style="font-size:13px">Brightpath<br>Record Renewal</div>
  </div>
  <nav class="abs footer-nav">
    <span style="left:0;color:var(--navy);font-weight:700;text-decoration:underline;text-underline-offset:6px">Home</span>
    <span style="left:57px">About Us</span>
    <span style="left:135px">Services</span>
    <span style="left:207px">Benefits</span>
    <span style="left:279px">Testimonials</span>
    <span style="left:383px">Contact US</span>
  </nav>
  <div class="abs copyright-band"></div>
  <p class="abs copyright">Copyright 2023 © Brightpathrecordrenewal Law Legal..</p>
</footer>

</body>
</html>
```